web page look and feel - B2B enterprise application

We have an enterprise application with 10 to 15 core pages and several supporting pages or popups. To start, we want the graphical design of the Users, Roles and Data Source pages and their supporting popups, wizards, etc. to be made beautiful. That is around 10 pages in total. There is a fair amount of redundancy among the pages. I have attached 5 screenshots. We very much want the pages to project a premium feel. That is absolutely essential. The color scheme is blue and sometimes yellow (only if it makes the page look better) plus black, gray and white. If the design of these screens goes well, we would expand the project to continue with other pages. The core of what we are looking for is graphic in nature but we are open to workflow suggestions if you have them. The Roles screen needs some improvements to the layout. I am looking for everything that includes icons, fonts, spacing, etc. I assume getting to the final design will take some back and forth with multiple revisions.

Target Market(s)

Large Enterprises

Number of Pages Required

5+ page

Requirements
Must have
• Premium feel

```html
<!DOCTYPE html>
<html lang="en">
<head>
<meta charset="utf-8">
<title>Corvane Data – Admin Screens</title>
<link href="https://fonts.googleapis.com/css2?family=Lato:wght@400;700;900&display=swap" rel="stylesheet">
<style>
:root{
  --stage:#4a7428;
  --navy:#30344f;
  --navy-deep:#272a42;
  --navy-line:#3c405d;
  --ink:#2b2d3a;
  --text:#4a4c57;
  --muted:#8b8d97;
  --line:#e2e3e8;
  --panel:#ffffff;
  --canvas:#f5f5f7;
  --head:#f0f1f4;
  --yellow:#f6b716;
  --blue:#1f9be3;
  --link:#3aa7e8;
  --green:#5fae1d;
  --red:#e0322b;
}
*{box-sizing:border-box;margin:0;padding:0}
html,body{width:1200px;height:695px;overflow:hidden}
body{background:var(--stage);font-family:"Lato",Arial,sans-serif;color:var(--text);position:relative}
svg.i{display:inline-block;vertical-align:middle}

.screen{position:absolute;overflow:hidden;background:var(--canvas);box-shadow:0 2px 8px rgba(0,0,0,.25)}
.screen--users{left:69px;top:22px;width:601px;height:300px}
.screen--roles{left:243px;top:345px;width:714px;height:300px}
.screen--sources{left:733px;top:22px;width:600px;height:452px;transform:scale(.6633);transform-origin:0 0}

/* top bar */
.topbar{position:absolute;left:0;top:0;right:0;height:30px;background:var(--navy);display:flex;align-items:center;color:#fff}
.brand{width:106px;height:30px;display:flex;align-items:center;justify-content:center;gap:5px;background:var(--navy-deep);font-weight:700;font-size:10px;letter-spacing:.1px}
.brand-dot{width:8px;height:8px;border-radius:50%;background:var(--yellow)}
.menu-btn{margin-left:9px;width:9px;height:9px}
.tools{margin-left:auto;display:flex;align-items:center;gap:9px;padding-right:10px;font-size:6px}
.tools svg{width:9px;height:9px}
.account{display:flex;align-items:center;gap:3px;margin-left:2px}
.account svg{width:5px;height:5px}

/* sidebar */
.sidebar{position:absolute;left:0;top:30px;bottom:0;width:106px;background:var(--navy);color:#e9eaf0;font-size:6.2px;padding-top:9px}
.nav-group{padding:0 0 4px 9px;margin-bottom:3px;border-bottom:1px solid var(--navy-line)}
.nav-group:last-of-type{border-bottom:none}
.nav-main,.nav-sub{height:12px;display:flex;align-items:center}
.nav-main .ico{width:5px;height:5px;border-radius:1px;background:var(--yellow);margin-right:9px}
.nav-main .caret{margin-left:auto;margin-right:12px;font-size:6px;color:#c8c9d3}
.nav-sub{color:var(--link)}
.nav-sub::before{content:"»";color:#c8c9d3;margin-right:11px;font-size:6px}
.is-active{color:var(--yellow)}
.legal{position:absolute;left:10px;bottom:34px;font-size:5px;line-height:8px;color:#b7b9c6}
.social{position:absolute;left:10px;bottom:12px;display:flex;gap:8px}
.social span{width:6px;height:6px;border-radius:50%;background:#8d90a6}

/* main */
.main{position:absolute;left:106px;top:30px;right:0;bottom:0}
.page-head{display:flex;align-items:center;height:34px;padding:0 9px 0 10px}
.page-title{font-size:10px;font-weight:700;color:var(--ink);margin-right:9px}
.btn-add{background:var(--navy);color:var(--yellow);font-size:6px;font-weight:700;padding:3px 8px;border-radius:2px}
.search{margin-left:auto;display:flex;align-items:center}
.search-field{width:106px;height:12px;border:1px solid #d6d7dd;background:#fff;font-size:5.5px;color:var(--muted);padding:0 5px;display:flex;align-items:center}
.search-btn{width:13px;height:12px;background:var(--yellow);display:flex;align-items:center;justify-content:center}
.search-btn svg{width:7px;height:7px}
.adv{margin-left:12px;font-size:6px;color:var(--ink);text-decoration:underline}

.panel{background:var(--panel);border:1px solid var(--line);margin:0 9px}
table{border-collapse:collapse;width:100%;font-size:6px}
th{text-align:left;font-weight:700;color:var(--ink);height:15px;padding:0 7px;border-bottom:1px solid var(--line)}
td{height:15px;padding:0 7px;border-bottom:1px solid #eeeff2}
th.sort::after{content:"⇅";float:right;color:#777;font-size:6px}
th.is-sorted{background:var(--blue);color:#fff}
th.is-sorted::after{color:#fff}
.status-on{color:var(--green)}
.status-off{color:var(--red)}
.actions{white-space:nowrap}
.actions svg{width:7px;height:7px;margin-right:6px}
.expander svg{width:5px;height:5px}

.detail-row td{padding:1px 4px 6px;border-bottom:1px solid #eeeff2}
.detail{border:1px solid var(--line)}
.detail table td{border-bottom:none;height:16px;padding:0 6px}
.detail .detail-head td{background:var(--head);font-weight:700;color:var(--ink);height:16px}
.cb{display:inline-block;width:5px;height:5px;border-radius:1px;border:1px solid #b8bac3;background:#fff;vertical-align:middle;margin-right:4px;position:relative;top:-.5px}
.cb.on{background:var(--blue);border-color:var(--blue)}
.cb.on::after{content:"";position:absolute;left:1px;top:0;width:1.2px;height:2.4px;border:solid #fff;border-width:0 .8px .8px 0;transform:rotate(45deg)}
.perm{margin-right:8px}
.btn-edit{display:block;margin:3px auto 5px;width:30px;height:11px;background:var(--navy);color:var(--yellow);font-size:6px;font-weight:700;text-align:center;line-height:11px;border-radius:1px}

.pager{display:flex;align-items:center;justify-content:center;gap:6px;font-size:6px;margin-top:6px}
.pager svg{width:6px;height:6px}
.pager .current{background:var(--yellow);color:#fff;width:8px;height:8px;text-align:center;line-height:8px;border-radius:1px;font-weight:700}
.pager .size{border:1px solid #d6d7dd;background:#fff;height:10px;width:21px;display:flex;align-items:center;justify-content:space-between;padding:0 3px}
.pager .size svg{width:4px;height:4px}
.page-foot{position:absolute;right:10px;bottom:9px;font-size:5px;color:var(--muted)}

/* roles */
.roles-card{background:#fff;border:1px solid var(--line);margin:0 21px 0 9px;padding:4px 4px 14px;height:148px}
.roles-card .panel{margin:0}
.roles-card th{font-size:5.8px;padding:0 4px}
.roles-card td{font-size:5.6px;padding:0 4px;height:16px;white-space:nowrap}
.roles-card .perm{margin-right:5px}
.role-name{color:var(--ink)}
.roles-foot{position:absolute;left:300px;bottom:10px;font-size:5px;color:var(--muted)}

/* sources */
.screen--sources .page-head{padding-left:9px}
.ds td,.ds th{font-size:5px;height:14px;padding:0 6px}
.nest{margin:3px 6px 6px 28px;border:1px solid var(--line)}
.nest-bar{display:flex;align-items:center;height:16px;background:var(--head);font-size:5px;color:var(--ink);padding:0 4px}
.nest-bar .label{flex:1;text-align:center;font-weight:700}
.btn-obj{background:var(--navy);color:var(--yellow);font-size:5px;padding:3px 7px;border-radius:1px}
.nest-name{text-align:center;font-size:5px;font-weight:700;height:12px;line-height:12px;border-bottom:1px solid var(--line)}
.obj-row{display:flex;align-items:center;height:11px;font-size:5px;padding:0 6px;color:var(--ink);border-bottom:1px solid var(--line)}
.obj-row svg{width:4px;height:4px;margin-right:8px}
.obj-row .count{margin-left:auto;color:var(--text)}
.fields{margin-left:10px;border-left:1px solid var(--line)}
.fields-title{text-align:center;font-size:5px;font-weight:700;background:var(--head);height:12px;line-height:12px}
.fields table th{font-size:4.6px;height:11px;padding:0 4px}
.fields table td{font-size:4.6px;height:14.2px;padding:0 4px}
.rt{display:inline-flex;gap:1px;background:#c9cacf;padding:1px}
.rt i{display:block;width:5px;height:6px;background:#8a8c95}
.rt.hot i:nth-child(1){background:var(--blue)}
.rt.hot i:nth-child(2){background:var(--yellow)}
.rt.hot i:nth-child(3){background:#e55b7a}
.rt.hot i:nth-child(5){background:var(--green)}
.fields .actions svg{width:6px;height:6px;margin-right:4px}
</style>
</head>
<body>

<svg width="0" height="0" style="position:absolute" aria-hidden="true">
  <defs>
    <symbol id="i-menu" viewBox="0 0 10 10"><path d="M0 1.5h10M0 5h10M0 8.5h10" stroke="#fff" stroke-width="1.4"/></symbol>
    <symbol id="i-gauge" viewBox="0 0 10 10"><path d="M1 8a4 4 0 1 1 8 0" fill="none" stroke="#fff" stroke-width="1.1"/><path d="M5 8l2-3" stroke="#fff" stroke-width="1.1"/></symbol>
    <symbol id="i-wand" viewBox="0 0 10 10"><path d="M1 9l6-6" stroke="#fff" stroke-width="1.2"/><path d="M8 0.5v2M7 1.5h2" stroke="#fff" stroke-width=".8"/></symbol>
    <symbol id="i-help" viewBox="0 0 10 10"><circle cx="5" cy="5" r="4.6" fill="#fff"/><path d="M3.6 3.8a1.4 1.4 0 1 1 1.9 1.3c-.4.2-.5.5-.5.9" fill="none" stroke="#30344f" stroke-width="1"/><circle cx="5" cy="7.6" r=".6" fill="#30344f"/></symbol>
    <symbol id="i-gear" viewBox="0 0 10 10"><circle cx="5" cy="5" r="3" fill="none" stroke="#fff" stroke-width="2.2" stroke-dasharray="1.6 .8"/><circle cx="5" cy="5" r="1.6" fill="none" stroke="#fff" stroke-width="1.2"/></symbol>
    <symbol id="i-down" viewBox="0 0 10 10"><path d="M1.5 3.5L5 7l3.5-3.5" fill="none" stroke="currentColor" stroke-width="1.4"/></symbol>
    <symbol id="i-right" viewBox="0 0 10 10"><path d="M3.5 1.5L7 5l-3.5 3.5" fill="none" stroke="currentColor" stroke-width="1.4"/></symbol>
    <symbol id="i-search" viewBox="0 0 10 10"><circle cx="4.2" cy="4.2" r="3" fill="none" stroke="#fff" stroke-width="1.3"/><path d="M6.4 6.4L9 9" stroke="#fff" stroke-width="1.4"/></symbol>
    <symbol id="i-edit" viewBox="0 0 10 10"><rect x=".5" y=".5" width="9" height="9" rx="1" fill="#2b2d3a"/><path d="M3 7l.3-1.5L6.5 2.3l1.2 1.2L4.5 6.7z" fill="#fff"/></symbol>
    <symbol id="i-copy" viewBox="0 0 10 10"><rect x=".8" y="2.8" width="6.2" height="6.2" rx=".8" fill="none" stroke="#2b2d3a" stroke-width="1"/><path d="M3 1h5.2a.8.8 0 0 1 .8.8V7" fill="none" stroke="#2b2d3a" stroke-width="1"/></symbol>
    <symbol id="i-trash" viewBox="0 0 10 10"><path d="M1.5 2h7M4 2V1h2v1" stroke="#2b2d3a" stroke-width="1" fill="none"/><path d="M2.4 3h5.2l-.5 6.5H2.9z" fill="#2b2d3a"/></symbol>
    <symbol id="i-first" viewBox="0 0 10 10"><path d="M1.5 1v8" stroke="#2b2d3a" stroke-width="1.4"/><path d="M9 1L3 5l6 4z" fill="#2b2d3a"/></symbol>
    <symbol id="i-prev" viewBox="0 0 10 10"><path d="M5 1L0 5l5 4zM10 1L5 5l5 4z" fill="#2b2d3a"/></symbol>
    <symbol id="i-next" viewBox="0 0 10 10"><path d="M0 1l5 4-5 4zM5 1l5 4-5 4z" fill="#2b2d3a"/></symbol>
    <symbol id="i-last" viewBox="0 0 10 10"><path d="M1 1l6 4-6 4z" fill="#2b2d3a"/><path d="M8.5 1v8" stroke="#2b2d3a" stroke-width="1.4"/></symbol>
  </defs>
</svg>

<!-- ============ USERS ============ -->
<section class="screen screen--users">
  <header class="topbar">
    <div class="brand"><span class="brand-dot"></span>Corvane Data</div>
    <svg class="i menu-btn"><use href="#i-menu"/></svg>
    <div class="tools">
      <svg class="i"><use href="#i-gauge"/></svg><svg class="i"><use href="#i-wand"/></svg><svg class="i"><use href="#i-help"/></svg><svg class="i"><use href="#i-gear"/></svg>
      <span class="account">Ned Hollis <svg class="i" style="color:#fff"><use href="#i-down"/></svg></span>
    </div>
  </header>
  <nav class="sidebar">
    <div class="nav-group">
      <div class="nav-main is-active"><span class="ico"></span>User<span class="caret">›</span></div>
      <div class="nav-sub">Roles</div>
      <div class="nav-sub">Notification Groups</div>
    </div>
    <div class="nav-group">
      <div class="nav-main"><span class="ico"></span>Date Sources</div>
      <div class="nav-sub">Data Object Relationships</div>
    </div>
    <div class="nav-group"><div class="nav-main"><span class="ico"></span>Data Sets<span class="caret">›</span></div></div>
    <div class="nav-group"><div class="nav-main"><span class="ico"></span>Rule Sets</div></div>
    <div class="nav-group"><div class="nav-main"><span class="ico"></span>Schedules</div></div>
    <div class="nav-group">
      <div class="nav-main"><span class="ico"></span>Metadata Import/Export<span class="caret">›</span></div>
      <div class="nav-sub">Import</div>
      <div class="nav-sub">Export</div>
    </div>
    <p class="legal">Copyright ©2018 Company Name.<br>All Rights Reserved</p>
    <div class="social"><span></span><span></span><span></span><span></span><span></span></div>
  </nav>
  <main class="main" style="background:#fff">
    <div class="page-head">
      <h1 class="page-title">Users</h1><span class="btn-add">Add</span>
      <div class="search"><div class="search-field">Search...</div><div class="search-btn"><svg class="i"><use href="#i-search"/></svg></div></div>
      <span class="adv">Advanced Search</span>
    </div>
    <div class="panel">
      <table>
        <colgroup><col style="width:22px"><col style="width:70px"><col style="width:70px"><col style="width:89px"><col style="width:90px"><col style="width:75px"><col></colgroup>
        <tr><th></th><th class="sort is-sorted">First Name</th><th class="sort">Last Name</th><th class="sort">Username</th><th class="sort">Email Address</th><th class="sort">Status</th><th></th></tr>
        <tr><td class="expander"><svg class="i"><use href="#i-down"/></svg></td><td>tim</td><td>tim</td><td>tim.timtim</td><td>tim@corvanedata.com</td><td class="status-on">Active</td><td class="actions"><svg class="i"><use href="#i-edit"/></svg><svg class="i"><use href="#i-copy"/></svg><svg class="i"><use href="#i-trash"/></svg></td></tr>
        <tr class="detail-row"><td colspan="7">
          <div class="detail">
            <table>
              <colgroup><col style="width:236px"><col></colgroup>
              <tr class="detail-head"><td>Object</td><td>Permission</td></tr>
              <tr><td>System Settings</td><td><span class="cb on"></span><span class="perm">Read</span><span class="cb on"></span>Write</td></tr>
              <tr><td>Users</td><td><span class="cb on"></span><span class="perm">Read</span><span class="cb on"></span>Write</td></tr>
              <tr><td>Data Source</td><td>Role</td></tr>
              <tr><td>All Data Sources</td><td>System Adminstration</td></tr>
            </table>
            <span class="btn-edit">Edit</span>
          </div>
        </td></tr>
        <tr><td class="expander"><svg class="i"><use href="#i-down"/></svg></td><td>tim</td><td>tim</td><td>tim.timtim</td><td>tim@corvanedata.com</td><td class="status-on">Active</td><td class="actions"><svg class="i"><use href="#i-edit"/></svg><svg class="i"><use href="#i-copy"/></svg><svg class="i"><use href="#i-trash"/></svg></td></tr>
        <tr><td class="expander"><svg class="i"><use href="#i-down"/></svg></td><td>tim</td><td>tim</td><td>tim.timtim</td><td>tim@corvanedata.com</td><td class="status-on">Active</td><td class="actions"><svg class="i"><use href="#i-edit"/></svg><svg class="i"><use href="#i-copy"/></svg><svg class="i"><use href="#i-trash"/></svg></td></tr>
        <tr><td class="expander"><svg class="i"><use href="#i-down"/></svg></td><td>tim</td><td>tim</td><td>tim.timtim</td><td>tim@corvanedata.com</td><td class="status-off">In Active</td><td class="actions"><svg class="i"><use href="#i-edit"/></svg><svg class="i"><use href="#i-copy"/></svg><svg class="i"><use href="#i-trash"/></svg></td></tr>
        <tr><td class="expander"><svg class="i"><use href="#i-down"/></svg></td><td>tim</td><td>tim</td><td>tim.timtim</td><td>tim@corvanedata.com</td><td class="status-on">Active</td><td class="actions"><svg class="i"><use href="#i-edit"/></svg><svg class="i"><use href="#i-copy"/></svg><svg class="i"><use href="#i-trash"/></svg></td></tr>
      </table>
    </div>
    <div class="pager"><svg class="i"><use href="#i-first"/></svg><svg class="i"><use href="#i-prev"/></svg><span class="current">1</span><svg class="i"><use href="#i-next"/></svg><svg class="i"><use href="#i-last"/></svg><span class="size">20<svg class="i"><use href="#i-down"/></svg></span></div>
    <span class="page-foot">x10</span>
  </main>
</section>

<!-- ============ DATA SOURCES ============ -->
<section class="screen screen--sources">
  <header class="topbar">
    <div class="brand"><span class="brand-dot"></span>Corvane Data</div>
    <svg class="i menu-btn"><use href="#i-menu"/></svg>
    <div class="tools">
      <svg class="i"><use href="#i-gauge"/></svg><svg class="i"><use href="#i-wand"/></svg><svg class="i"><use href="#i-help"/></svg><svg class="i"><use href="#i-gear"/></svg>
      <span class="account">Ned Hollis <svg class="i" style="color:#fff"><use href="#i-down"/></svg></span>
    </div>
  </header>
  <nav class="sidebar">
    <div class="nav-group">
      <div class="nav-main"><span class="ico"></span>User<span class="caret">›</span></div>
      <div class="nav-sub">Roles</div>
      <div class="nav-sub">Notification Groups</div>
    </div>
    <div class="nav-group">
      <div class="nav-main is-active"><span class="ico"></span>Date Sources</div>
      <div class="nav-sub">Data Object Relationships</div>
    </div>
    <div class="nav-group"><div class="nav-main"><span class="ico"></span>Data Sets<span class="caret">›</span></div></div>
    <div class="nav-group"><div class="nav-main"><span class="ico"></span>Rule Sets</div></div>
    <div class="nav-group"><div class="nav-main"><span class="ico"></span>Schedules</div></div>
    <div class="nav-group">
      <div class="nav-main"><span class="ico"></span>Metadata Import/Export<span class="caret">›</span></div>
      <div class="nav-sub">Import</div>
      <div class="nav-sub">Export</div>
    </div>
    <p class="legal" style="bottom:28px">Copyright ©2018 Company Name.<br>All Rights Reserved</p>
    <div class="social"><span></span><span></span><span></span><span></span><span></span></div>
  </nav>
  <main class="main" style="background:#fff">
    <div class="page-head">
      <h1 class="page-title">Data Sources</h1><span class="btn-add">Add</span>
      <div class="search"><div class="search-field">Search...</div><div class="search-btn"><svg class="i"><use href="#i-search"/></svg></div></div>
      <span class="adv">Advanced Search</span>
    </div>
    <div class="panel" style="margin-right:4px">
      <table class="ds">
        <colgroup><col style="width:22px"><col style="width:116px"><col style="width:137px"><col style="width:137px"><col></colgroup>
        <tr><th></th><th class="sort">Data Source Name</th><th class="sort">Type</th><th class="sort">Status</th><th></th></tr>
        <tr><td class="expander"><svg class="i"><use href="#i-right"/></svg></td><td>RelStore</td><td>tim.timtim</td><td class="status-on">Active</td><td class="actions"><svg class="i"><use href="#i-edit"/></svg><svg class="i"><use href="#i-trash"/></svg></td></tr>
        <tr><td class="expander"><svg class="i"><use href="#i-down"/></svg></td><td>CRMH</td><td>crmhub.io</td><td class="status-on">Active</td><td class="actions"><svg class="i"><use href="#i-edit"/></svg><svg class="i"><use href="#i-trash"/></svg></td></tr>
      </table>
      <div class="nest">
        <div class="nest-bar"><span class="label">Permission</span><span class="btn-obj">Add Data Object</span></div>
        <div class="nest-name">Name</div>
        <div class="obj-row"><svg class="i"><use href="#i-down"/></svg>Account<span class="count">19 Fields</span></div>
        <div class="fields">
          <div class="fields-title">Fields</div>
          <table>
            <colgroup><col style="width:164px"><col style="width:117px"><col style="width:45px"><col style="width:72px"><col></colgroup>
            <tr><th>Field Name</th><th>Data Type</th><th>Primary Key</th><th>Role Types</th><th></th></tr>
            <tr><td>AccountFax</td><td></td><td></td><td><span class="rt"><i></i><i></i><i></i><i></i><i></i><i></i></span></td><td class="actions"><svg class="i"><use href="#i-edit"/></svg><svg class="i"><use href="#i-trash"/></svg></td></tr>
            <tr><td>AccountID</td><td>Address 1</td><td></td><td><span class="rt hot"><i></i><i></i><i></i><i></i><i></i><i></i></span></td><td class="actions"><svg class="i"><use href="#i-edit"/></svg><svg class="i"><use href="#i-trash"/></svg></td></tr>
            <tr><td>Account Name</td><td></td><td></td><td><span class="rt"><i></i><i></i><i></i><i></i><i></i><i></i></span></td><td class="actions"><svg class="i"><use href="#i-edit"/></svg><svg class="i"><use href="#i-trash"/></svg></td></tr>
            <tr><td>Billing City</td><td></td><td></td><td><span class="rt"><i></i><i></i><i></i><i></i><i></i><i></i></span></td><td class="actions"><svg class="i"><use href="#i-edit"/></svg><svg class="i"><use href="#i-trash"/></svg></td></tr>
            <tr><td>Billing Country</td><td></td><td></td><td><span class="rt"><i></i><i></i><i></i><i></i><i></i><i></i></span></td><td class="actions"><svg class="i"><use href="#i-edit"/></svg><svg class="i"><use href="#i-trash"/></svg></td></tr>
            <tr><td>Billing Latitude</td><td></td><td></td><td><span class="rt"><i></i><i></i><i></i><i></i><i></i><i></i></span></td><td class="actions"><svg class="i"><use href="#i-edit"/></svg><svg class="i"><use href="#i-trash"/></svg></td></tr>
            <tr><td>Billing Longitude</td><td></td><td></td><td><span class="rt"><i></i><i></i><i></i><i></i><i></i><i></i></span></td><td class="actions"><svg class="i"><use href="#i-edit"/></svg><svg class="i"><use href="#i-trash"/></svg></td></tr>
            <tr><td>Billing state/Province</td><td></td><td></td><td><span class="rt"><i></i><i></i><i></i><i></i><i></i><i></i></span></td><td class="actions"><svg class="i"><use href="#i-edit"/></svg><svg class="i"><use href="#i-trash"/></svg></td></tr>
            <tr><td>Billing street</td><td></td><td></td><td><span class="rt"><i></i><i></i><i></i><i></i><i></i><i></i></span></td><td class="actions"><svg class="i"><use href="#i-edit"/></svg><svg class="i"><use href="#i-trash"/></svg></td></tr>
            <tr><td>Billing Zip/Postal Code</td><td></td><td></td><td><span class="rt"><i></i><i></i><i></i><i></i><i></i><i></i></span></td><td class="actions"><svg class="i"><use href="#i-edit"/></svg><svg class="i"><use href="#i-trash"/></svg></td></tr>
            <tr><td>Last Modified Date</td><td></td><td></td><td><span class="rt"><i></i><i></i><i></i><i></i><i></i><i></i></span></td><td class="actions"><svg class="i"><use href="#i-edit"/></svg><svg class="i"><use href="#i-trash"/></svg></td></tr>
            <tr><td>ShippingCity</td><td></td><td></td><td><span class="rt"><i></i><i></i><i></i><i></i><i></i><i></i></span></td><td class="actions"><svg class="i"><use href="#i-edit"/></svg><svg class="i"><use href="#i-trash"/></svg></td></tr>
            <tr><td>ShippingCountry</td><td></td><td></td><td><span class="rt"><i></i><i></i><i></i><i></i><i></i><i></i></span></td><td class="actions"><svg class="i"><use href="#i-edit"/></svg><svg class="i"><use href="#i-trash"/></svg></td></tr>
            <tr><td>Shipping Latitude</td><td></td><td></td><td><span class="rt"><i></i><i></i><i></i><i></i><i></i><i></i></span></td><td class="actions"><svg class="i"><use href="#i-edit"/></svg><svg class="i"><use href="#i-trash"/></svg></td></tr>
            <tr><td>Shipping Longitude</td><td></td><td></td><td><span class="rt"><i></i><i></i><i></i><i></i><i></i><i></i></span></td><td class="actions"><svg class="i"><use href="#i-edit"/></svg><svg class="i"><use href="#i-trash"/></svg></td></tr>
            <tr><td>Shippingstate/Province</td><td></td><td></td><td><span class="rt"><i></i><i></i><i></i><i></i><i></i><i></i></span></td><td class="actions"><svg class="i"><use href="#i-edit"/></svg><svg class="i"><use href="#i-trash"/></svg></td></tr>
          </table>
        </div>
      </div>
    </div>
    <span class="page-foot" style="bottom:4px">x10</span>
  </main>
</section>

<!-- ============ ROLES ============ -->
<section class="screen screen--roles">
  <header class="topbar">
    <div class="brand"><span class="brand-dot"></span>Corvane Data</div>
    <svg class="i menu-btn"><use href="#i-menu"/></svg>
    <div class="tools">
      <svg class="i"><use href="#i-gauge"/></svg><svg class="i"><use href="#i-wand"/></svg><svg class="i"><use href="#i-help"/></svg><svg class="i"><use href="#i-gear"/></svg>
      <span class="account">Ned Hollis <svg class="i" style="color:#fff"><use href="#i-down"/></svg></span>
    </div>
  </header>
  <nav class="sidebar">
    <div class="nav-group">
      <div class="nav-main"><span class="ico"></span>User<span class="caret">›</span></div>
      <div class="nav-sub is-active">Roles</div>
      <div class="nav-sub">Notification Groups</div>
    </div>
    <div class="nav-group">
      <div class="nav-main"><span class="ico"></span>Date Sources</div>
      <div class="nav-sub">Data Object Relationships</div>
    </div>
    <div class="nav-group"><div class="nav-main"><span class="ico"></span>Data Sets<span class="caret">›</span></div></div>
    <div class="nav-group"><div class="nav-main"><span class="ico"></span>Rule Sets</div></div>
    <div class="nav-group"><div class="nav-main"><span class="ico"></span>Schedules</div></div>
    <div class="nav-group">
      <div class="nav-main"><span class="ico"></span>Metadata Import/Export<span class="caret">›</span></div>
      <div class="nav-sub">Import</div>
      <div class="nav-sub">Export</div>
    </div>
    <p class="legal">Copyright ©2018 Company Name.<br>All Rights Reserved</p>
    <div class="social"><span></span><span></span><span></span><span></span><span></span></div>
  </nav>
  <main class="main" style="background:#fff">
    <div class="roles-card" style="margin-top:5px">
      <div class="page-head" style="padding:0 0 0 4px;height:32px">
        <h1 class="page-title">Role</h1><span class="btn-add">Add</span>
        <div class="search"><div class="search-field">Search...</div><div class="search-btn"><svg class="i"><use href="#i-search"/></svg></div></div>
        <span class="adv">Advanced Search</span>
      </div>
      <div class="panel">
        <table>
          <colgroup><col style="width:61px"><col style="width:55px"><col style="width:54px"><col style="width:54px"><col style="width:54px"><col style="width:54px"><col style="width:60px"><col style="width:74px"><col style="width:54px"><col></colgroup>
          <tr><th class="sort">Role Name</th><th>Data Sources</th><th>Data Sets</th><th>Rule Sets</th><th>Schedule</th><th>Suspect Matches</th><th>Master Data Object</th><th>Metadata Import/Export</th><th>API</th><th></th></tr>
          <tr><td class="role-name">System Adminstrator</td>
            <td><span class="cb on"></span><span class="perm">Read</span><span class="cb on"></span>Write</td>
            <td><span class="cb on"></span><span class="perm">Read</span><span class="cb on"></span>Write</td>
            <td><span class="cb on"></span><span class="perm">Read</span><span class="cb on"></span>Write</td>
            <td><span class="cb on"></span><span class="perm">Read</span><span class="cb on"></span>Write</td>
            <td><span class="cb on"></span><span class="perm">Read</span><span class="cb on"></span>Write</td>
            <td><span class="cb on"></span><span class="perm">Read</span><span class="cb on"></span>Write</td>
            <td><span class="cb on"></span><span class="perm">Read</span><span class="cb on"></span>Write</td>
            <td><span class="cb on"></span><span class="perm">Read</span><span class="cb on"></span>Write</td>
            <td class="actions"><svg class="i"><use href="#i-copy"/></svg></td></tr>
          <tr><td class="role-name">Role #1</td>
            <td><span class="cb"></span><span class="perm">Read</span><span class="cb"></span>Write</td>
            <td><span class="cb"></span><span class="perm">Read</span><span class="cb"></span>Write</td>
            <td><span class="cb"></span><span class="perm">Read</span><span class="cb"></span>Write</td>
            <td><span class="cb"></span><span class="perm">Read</span><span class="cb"></span>Write</td>
            <td><span class="cb"></span><span class="perm">Read</span><span class="cb"></span>Write</td>
            <td><span class="cb"></span><span class="perm">Read</span><span class="cb"></span>Write</td>
            <td><span class="cb"></span><span class="perm">Read</span><span class="cb"></span>Write</td>
            <td><span class="cb"></span><span class="perm">Read</span><span class="cb"></span>Write</td>
            <td class="actions"><svg class="i"><use href="#i-copy"/></svg></td></tr>
          <tr><td class="role-name">Read Only</td>
            <td><span class="cb on"></span><span class="perm">Read</span><span class="cb"></span>Write</td>
            <td><span class="cb on"></span><span class="perm">Read</span><span class="cb"></span>Write</td>
            <td><span class="cb on"></span><span class="perm">Read</span><span class="cb"></span>Write</td>
            <td><span class="cb on"></span><span class="perm">Read</span><span class="cb"></span>Write</td>
            <td><span class="cb on"></span><span class="perm">Read</span><span class="cb"></span>Write</td>
            <td><span class="cb on"></span><span class="perm">Read</span><span class="cb"></span>Write</td>
            <td><span class="cb on"></span><span class="perm">Read</span><span class="cb"></span>Write</td>
            <td><span class="cb on"></span><span class="perm">Read</span><span class="cb"></span>Write</td>
            <td class="actions"><svg class="i"><use href="#i-edit"/></svg><svg class="i"><use href="#i-copy"/></svg><svg class="i"><use href="#i-trash"/></svg></td></tr>
          <tr><td class="role-name">Data Administor</td>
            <td><span class="cb"></span><span class="perm">Read</span><span class="cb"></span>Write</td>
            <td><span class="cb"></span><span class="perm">Read</span><span class="cb"></span>Write</td>
            <td><span class="cb"></span><span class="perm">Read</span><span class="cb"></span>Write</td>
            <td><span class="cb"></span><span class="perm">Read</span><span class="cb"></span>Write</td>
            <td><span class="cb"></span><span class="perm">Read</span><span class="cb"></span>Write</td>
            <td><span class="cb"></span><span class="perm">Read</span><span class="cb"></span>Write</td>
            <td><span class="cb"></span><span class="perm">Read</span><span class="cb"></span>Write</td>
            <td><span class="cb"></span><span class="perm">Read</span><span class="cb"></span>Write</td>
            <td class="actions"><svg class="i"><use href="#i-copy"/></svg></td></tr>
        </table>
      </div>
      <div class="pager" style="margin-top:9px"><svg class="i"><use href="#i-first"/></svg><svg class="i"><use href="#i-prev"/></svg><span class="current">1</span><svg class="i"><use href="#i-next"/></svg><svg class="i"><use href="#i-last"/></svg><span class="size">10<svg class="i"><use href="#i-down"/></svg></span></div>
    </div>
    <span class="roles-foot">x10</span>
  </main>
</section>

</body>
</html>
```